VOR Exterior Coatings

double sided. the front i want the name of the business each word on a new line with the VOR being bigger. id like teal, black and white colors. the back i want my contact info. Flat, no gloss. Something professional and I want to feel the letters bump put of the card. if possible maybe a paint sprayer in corner. not a car paint spray. (no tank on top of gun)
no vehicle paint sprayers. that means no tank on top of the gun. doesn't have to have a sprayer. black/dark background on the front. white back ground on back with info

```html
<!DOCTYPE html>
<html lang="en">
<head>
<meta charset="UTF-8">
<title>VOR Exterior Coatings – Business Cards</title>
<link rel="stylesheet" href="https://fonts.googleapis.com/css2?family=Open+Sans:wght@400;600;700;800&display=swap">
<style>
  :root {
    --stage: #3a3a3c;
    --card-black: #0a0a0a;
    --card-black-2: #161616;
    --card-white: #ffffff;
    --card-white-2: #f3f3f3;
    --ink: #141414;
    --teal: #22a7ab;
    --white: #ffffff;
  }
  * { box-sizing: border-box; margin: 0; padding: 0; }
  html, body {
    width: 1200px; height: 900px; overflow: hidden;
    background: var(--stage);
    font-family: "Open Sans", Arial, sans-serif;
  }
  .stage {
    position: relative; width: 1200px; height: 900px;
    display: flex; flex-direction: column; align-items: center; justify-content: center; gap: 36px;
  }
  .card {
    position: relative; width: 736px; height: 404px;
    border-radius: 4px; overflow: hidden;
    box-shadow: 0 14px 30px rgba(0,0,0,0.45);
  }

  /* Front */
  .front { background: linear-gradient(135deg, var(--card-black) 0%, var(--card-black-2) 100%); }
  .front .brand {
    position: absolute; left: 170px; top: 118px;
    line-height: 1;
  }
  .front .brand-row { display: flex; align-items: center; gap: 16px; }
  .front .brand-name { color: var(--white); font-weight: 700; font-size: 112px; letter-spacing: 2px; }
  .brand-mark { width: 22px; height: 22px; background: var(--teal); flex: none; }
  .front .brand-tagline {
    color: var(--teal); font-weight: 600; font-size: 21px; letter-spacing: 3px; margin-top: 8px;
  }
  .front .sprayer-art {
    position: absolute; left: 520px; top: 70px; width: 180px; height: 230px;
    background: linear-gradient(160deg, rgba(255,255,255,0.22), rgba(255,255,255,0.06));
    border-radius: 6px;
  }

  /* Back */
  .back { background: linear-gradient(135deg, var(--card-white) 0%, var(--card-white-2) 100%); }
  .back .brand-row {
    position: absolute; left: 60px; top: 34px;
    display: flex; align-items: center; gap: 18px;
  }
  .back .brand-name {
    color: var(--ink); font-weight: 700; font-size: 140px; line-height: 1; letter-spacing: 4px;
  }
  .back .brand-mark { width: 26px; height: 26px; }
  .back .sprayer-art {
    position: absolute; right: 40px; top: 28px; width: 180px; height: 150px;
    background: linear-gradient(160deg, rgba(0,0,0,0.08), rgba(0,0,0,0.02));
    border-radius: 6px;
  }
  .back .divider {
    position: absolute; left: 60px; right: 78px; top: 248px; height: 2px; background: var(--ink);
  }
  .contact-list {
    position: absolute; left: 60px; top: 272px; list-style: none;
    color: var(--ink); font-size: 23px; line-height: 34px;
  }
  .contact-list li { display: flex; align-items: center; gap: 12px; }
  .contact-list svg { width: 20px; height: 20px; flex: none; }
  .person {
    position: absolute; right: 78px; top: 196px; text-align: right; color: var(--ink);
  }
  .person-name {
    color: var(--teal); font-weight: 700; font-size: 34px; letter-spacing: 1px; line-height: 44px;
  }
  .person-role { font-size: 23px; line-height: 30px; margin-top: 26px; }
  .person-address { font-size: 23px; line-height: 30px; margin-top: 4px; }
</style>
</head>
<body>
<main class="stage">

  <section class="card front" aria-label="Card front">
    <div class="sprayer-art" role="img" aria-label="Line illustration of a handheld paint spray gun spraying outward"></div>
    <div class="brand">
      <div class="brand-row">
        <div class="brand-name">VOR</div>
        <span class="brand-mark" aria-hidden="true"></span>
      </div>
      <div class="brand-tagline">EXTERIOR COATINGS</div>
    </div>
  </section>

  <section class="card back" aria-label="Card back">
    <div class="sprayer-art" role="img" aria-label="Faint line illustration of a handheld paint spray gun"></div>
    <div class="brand-row">
      <div class="brand-name">VOR</div>
      <span class="brand-mark" aria-hidden="true"></span>
    </div>
    <div class="divider"></div>

    <ul class="contact-list">
      <li>
        <svg viewBox="0 0 24 24" aria-hidden="true"><path fill="var(--teal)" d="M6.6 10.8a15.1 15.1 0 0 0 6.6 6.6l2.2-2.2a1 1 0 0 1 1-.25 11.4 11.4 0 0 0 3.6.57 1 1 0 0 1 1 1V20a1 1 0 0 1-1 1A17 17 0 0 1 3 4a1 1 0 0 1 1-1h3.5a1 1 0 0 1 1 1c0 1.25.2 2.45.57 3.6a1 1 0 0 1-.25 1z"/></svg>
        555-014-2100
      </li>
      <li>
        <svg viewBox="0 0 24 24" aria-hidden="true"><rect x="2" y="5" width="20" height="14" rx="1.5" fill="var(--teal)"/><path d="M3 6l9 7 9-7" stroke="var(--white)" stroke-width="1.6" fill="none"/></svg>
        hello@vorcoatings.com
      </li>
      <li>
        <svg viewBox="0 0 24 24" aria-hidden="true"><circle cx="12" cy="12" r="9.5" fill="var(--teal)"/><path d="M2.5 12h19M12 2.5c3 3 3 16 0 19M12 2.5c-3 3-3 16 0 19" stroke="var(--white)" stroke-width="1.4" fill="none"/></svg>
        www.vorcoatings.com
      </li>
    </ul>

    <div class="person">
      <div class="person-name">MARCUS HALE</div>
      <div class="person-role">Manager</div>
      <div class="person-address">Your address, city<br>state, ZIP 0000</div>
    </div>
  </section>

</main>
</body>
</html>
```